Album Cover for Tunevale/Orchard Sound Neoclassical

I would like to get a new album cover design for a new release called 'Veldarine' by Tom Harwick. <br/>Some creative pointers - <br/>The meaning of veldarine is "the desire to care less about things..." to be a child again to be totally free. <br/>It is an album of upright piano solo pieces so perhaps some hint of an old retro upright piano as well as a sense of freedom. <br/>I like bright colour but equally I also like simple black & white.<br/>I am a fan of Lena Sorbeck and Pavel Ostrani so perhaps look at some of their covers as a guide. <br/>

Target Market(s)

20-40 yr old m&f - fans of Tobias Vennmark or Lena Sorbeck

Font styles to use
Serif

Colors

Designer to choose colors to be used in the design.

Requirements
Must have
• a sense of piano classical but more cinematic than formal/traditional classical
• Also a sense of freedom as above
Nice to have
• something modern looking as if it were a pop track but for classical
Should not have
• nothing too dark grey, dark green, dark sombre feel

```html
<!DOCTYPE html>
<html lang="en">
<head>
<meta charset="utf-8">
<title>Veldarine — Tom Harwick</title>
<link rel="stylesheet" href="https://fonts.googleapis.com/css2?family=Tinos:wght@700&family=Raleway:wght@300&display=swap">
<style>
  :root {
    --page-bg: #dedede;
    --cover-navy: #003a5c;
    --cover-deep: #00263d;
    --frame-white: #ffffff;
    --photo-bright: rgba(236, 240, 244, 0.92);
    --photo-light: rgba(205, 212, 222, 0.75);
    --photo-mid: rgba(150, 160, 178, 0.5);
    --photo-haze: rgba(92, 78, 96, 0.6);
  }
  html, body {
    margin: 0;
    padding: 0;
    width: 1200px;
    height: 1026px;
    overflow: hidden;
    background: var(--page-bg);
  }
  .album-cover {
    position: absolute;
    left: 130px;
    top: 43px;
    width: 940px;
    height: 940px;
    background: var(--cover-navy);
    overflow: hidden;
  }
  .cover-photo {
    position: absolute;
    left: 34%;
    top: 0;
    right: 0;
    bottom: 0;
    background:
      /* light on the instrument body, right middle */
      radial-gradient(ellipse 42% 26% at 74% 46%, var(--photo-bright), rgba(0, 58, 92, 0) 80%),
      /* raised lid catching light, upper right */
      linear-gradient(128deg, rgba(0, 58, 92, 0) 62%, var(--photo-light) 76%, rgba(0, 58, 92, 0) 90%),
      /* stool highlight, lower centre */
      radial-gradient(ellipse 18% 9% at 22% 65%, var(--photo-light), rgba(0, 58, 92, 0) 85%),
      /* lit floor under the piano */
      radial-gradient(ellipse 55% 10% at 62% 79%, var(--photo-mid), rgba(0, 58, 92, 0) 85%),
      /* legs and lower body */
      radial-gradient(ellipse 20% 22% at 88% 74%, var(--photo-mid), rgba(0, 58, 92, 0) 85%),
      /* warm stage haze at the top */
      radial-gradient(ellipse 70% 28% at 65% 8%, var(--photo-haze), rgba(0, 58, 92, 0) 80%);
  }
  .cover-frame {
    position: absolute;
    inset: 25px;
    border: 2px solid var(--frame-white);
  }
  .album-title {
    position: absolute;
    left: 160px;
    top: 62px;
    margin: 0;
    font-family: "Tinos", "Times New Roman", serif;
    font-weight: 700;
    font-size: 110px;
    line-height: 1;
    color: var(--frame-white);
  }
  .artist-name {
    position: absolute;
    left: 0;
    right: 0;
    top: 848px;
    margin: 0;
    text-align: center;
    font-family: "Raleway", "Helvetica Neue", sans-serif;
    font-weight: 300;
    font-size: 42px;
    line-height: 1;
    letter-spacing: 0.42em;
    padding-left: 0.42em;
    color: var(--frame-white);
  }
</style>
</head>
<body>
  <main class="album-cover">
    <div class="cover-photo" role="img" aria-label="Photograph of a white grand piano with its lid raised and a tufted piano stool, lit on a dark stage floor"></div>
    <div class="cover-frame"></div>
    <h1 class="album-title">VELDARINE</h1>
    <p class="artist-name">TOM HARWICK</p>
  </main>
</body>
</html>
```